Salon and Spa Distributor Business Card

Need a business card. We are are distributor in the salon and spa industry. We identify with natural beauty. Need a card with:
Company Name: Petal Quarry"
Title: "President & CEO"
Address
Company Phone number
email
website
Tag Line:" The Professional Salon Source"

Industry/Entity Type

Business

Contact Information for Business Card

Name: Dov Strommen
Title: "President & CEO"
Address: 31 Harlow Ln, Bexmoor, NJ 07813
Company Phone number: 800-463-5918
email: dovstrommen@petalquarry.example
website: www.petalquarry.example

Requirements
Should not have
• No black backgrounds

```html
<!DOCTYPE html>
<html lang="en">
<head>
<meta charset="utf-8">
<title>Petal Quarry — Business Card</title>
<link rel="stylesheet" href="https://fonts.googleapis.com/css2?family=Didact+Gothic&family=PT+Sans+Narrow&family=Tinos&display=swap">
<style>
  :root {
    --stage: #4b4b4b;
    --green: #62b946;
    --green-light: #6cc350;
    --green-deep: #3f8a37;
    --wordmark: #4e8f3f;
    --white: #ffffff;
    --card-white: #fdfdfd;
    --card-shade: #ececec;
    --ink: #1d1d1d;
    --name-green: #3f9a3a;
  }
  * { margin: 0; padding: 0; box-sizing: border-box; }
  html, body {
    width: 1200px;
    height: 997px;
    overflow: hidden;
  }
  body {
    background: var(--stage);
    position: relative;
    font-family: "Didact Gothic", sans-serif;
  }
  .card {
    position: absolute;
    top: 350px;
    width: 526px;
    height: 315px;
    border-radius: 14px;
    overflow: hidden;
  }
  .card--front {
    left: 66px;
    background: radial-gradient(ellipse at 45% 35%, var(--green-light) 0%, var(--green) 60%, #5bb040 100%);
  }
  .card--back {
    left: 614px;
    background: linear-gradient(120deg, var(--card-white) 55%, var(--card-shade) 100%);
  }
  .wordmark {
    position: absolute;
    left: 0;
    right: 0;
    top: 200px;
    text-align: center;
    font-family: "Didact Gothic", sans-serif;
    font-size: 46px;
    color: var(--wordmark);
    letter-spacing: 0.5px;
  }
  .tagline {
    position: absolute;
    left: 0;
    right: 0;
    top: 264px;
    text-align: center;
    font-family: "PT Sans Narrow", sans-serif;
    font-size: 22px;
    color: var(--white);
    letter-spacing: 1.5px;
  }
  .person {
    position: absolute;
    right: 35px;
    top: 28px;
    text-align: right;
  }
  .person__name {
    font-family: "Didact Gothic", sans-serif;
    font-size: 21px;
    color: var(--name-green);
    line-height: 1.1;
  }
  .person__title {
    font-family: "Tinos", serif;
    font-size: 15px;
    color: var(--ink);
    margin-top: 2px;
  }
  .contacts {
    position: absolute;
    right: 32px;
    top: 205px;
    list-style: none;
  }
  .contacts__item {
    display: flex;
    justify-content: flex-end;
    align-items: center;
    gap: 12px;
    height: 34px;
    font-size: 15px;
    color: var(--ink);
  }
  .contacts__icon {
    width: 22px;
    height: 22px;
    flex: none;
  }
</style>
</head>
<body>
  <section class="card card--front" aria-label="Card front">
    <p class="wordmark">Petal Quarry</p>
    <p class="tagline">The Professional Salon Source</p>
  </section>

  <section class="card card--back" aria-label="Card back">
    <div class="person">
      <p class="person__name">Dov Strommen</p>
      <p class="person__title">President &amp; CEO</p>
    </div>
    <ul class="contacts">
      <li class="contacts__item">
        <span>800-463-5918</span>
        <svg class="contacts__icon" viewBox="0 0 22 22" aria-hidden="true">
          <circle cx="11" cy="11" r="11" fill="var(--green-deep)"/>
          <path d="M6.5 8.5c0-1.2 2-2 4.5-2s4.5.8 4.5 2v1h-2.2v-1h-4.6v1H6.5z M7.5 10.5h7l1 5h-9z" fill="var(--white)"/>
          <circle cx="11" cy="13" r="1.4" fill="var(--green-deep)"/>
        </svg>
      </li>
      <li class="contacts__item">
        <span>dovstrommen@petalquarry.example</span>
        <svg class="contacts__icon" viewBox="0 0 22 22" aria-hidden="true">
          <circle cx="11" cy="11" r="11" fill="var(--green-deep)"/>
          <rect x="5.5" y="7" width="11" height="8" fill="var(--white)"/>
          <path d="M5.5 7l5.5 4.5L16.5 7" fill="none" stroke="var(--green-deep)" stroke-width="1.1"/>
        </svg>
      </li>
      <li class="contacts__item">
        <span>31 Harlow Ln, Bexmoor, NJ 07813</span>
        <svg class="contacts__icon" viewBox="0 0 22 22" aria-hidden="true">
          <circle cx="11" cy="11" r="11" fill="var(--green-deep)"/>
          <path d="M11 4.5a4.2 4.2 0 0 0-4.2 4.2c0 3.2 4.2 8.3 4.2 8.3s4.2-5.1 4.2-8.3A4.2 4.2 0 0 0 11 4.5z" fill="var(--white)"/>
          <circle cx="11" cy="8.7" r="1.6" fill="var(--green-deep)"/>
        </svg>
      </li>
    </ul>
  </section>
</body>
</html>
```